Business card for law firm

Need business card for new law firm. Think confident, authoritative, conservative, but not stuffy or old-fashioned.

Contact Information for Business Card

Content for card - logo (uploaded), plus the following:

Paul Whitcombe (larger font)
Managing Partner (larger font, but not as large as name)
Level 9, 7 Ferris Lane
Sydney NSW 2000
Main Tel 02 9364 2710
Direct Tel 02 8472 3159
Email paul@qvlegal.com.au
www.qvlegal.com.au

Letterhead design should include logo plus:
Level 9, 7 Ferris Lane
Sydney NSW 2000
Tel 02 8472 3159
www.qvlegal.com.au

```html
<!DOCTYPE html>
<html lang="en">
<head>
<meta charset="utf-8">
<title>Quayview Legal – Business Card</title>
<link rel="stylesheet" href="https://fonts.googleapis.com/css2?family=Cinzel:wght@400;500&family=Jost:wght@300;400&display=swap">
<style>
  :root {
    --navy: #0b1d57;
    --paper: #ffffff;
    --backdrop: #e4e4e4;
    --ink-grey: #6b6b6b;
    --rule-grey: #b9b9b9;
  }
  * { margin: 0; padding: 0; box-sizing: border-box; }
  html, body {
    width: 1125px; height: 1200px; overflow: hidden;
    background: var(--backdrop);
  }
  .card {
    position: absolute;
    left: 150px;
    width: 826px;
    height: 472px;
  }
  .card-front { top: 98px; background: var(--paper); }
  .card-back { top: 631px; background: var(--navy); }

  .identity {
    position: absolute;
    right: 413px;
    top: 198px;
    text-align: right;
    font-family: "Cinzel", serif;
  }
  .identity-name {
    color: var(--navy);
    font-size: 31px;
    font-weight: 500;
    line-height: 1.05;
  }
  .identity-title {
    color: var(--ink-grey);
    font-size: 19px;
    letter-spacing: 1px;
    margin-top: 2px;
  }
  .divider {
    position: absolute;
    left: 440px;
    top: 138px;
    width: 1px;
    height: 190px;
    background: var(--rule-grey);
  }
  .contact {
    position: absolute;
    left: 476px;
    top: 165px;
    font-family: "Jost", sans-serif;
    font-weight: 300;
    color: var(--ink-grey);
    font-size: 21px;
    line-height: 27px;
  }
  .contact-address { margin-bottom: 9px; }
  .contact-list { list-style: none; }
  .contact-list li { display: flex; align-items: center; }
  .contact-list svg { width: 20px; height: 20px; margin-right: 12px; fill: var(--navy); flex: none; }
  .contact-list .email { font-size: 19px; }

  .web-band {
    position: absolute;
    left: 0; right: 0;
    top: 402px;
    height: 40px;
    background: var(--navy);
    color: var(--paper);
    font-family: "Cinzel", serif;
    font-size: 19px;
    letter-spacing: 12px;
    text-align: center;
    line-height: 40px;
    text-transform: uppercase;
    padding-left: 12px;
  }

  .brand {
    position: absolute;
    left: 0; right: 0;
    top: 150px;
    text-align: center;
    color: var(--paper);
    font-family: "Cinzel", serif;
    font-weight: 400;
  }
  .brand-mark {
    display: block;
    width: 22px; height: 22px;
    margin: 0 auto 28px;
    background: var(--paper);
  }
  .brand-name { font-size: 62px; letter-spacing: 2px; line-height: 1; }
  .brand-sub { font-size: 22px; letter-spacing: 26px; margin-top: 14px; padding-left: 26px; }
</style>
</head>
<body>
  <section class="card card-front">
    <div class="identity">
      <p class="identity-name">Paul Whitcombe</p>
      <p class="identity-title">Managing Partner</p>
    </div>
    <div class="divider"></div>
    <div class="contact">
      <p class="contact-address">Level 9, 7 Ferris Lane<br>Sydney NSW 2000</p>
      <ul class="contact-list">
        <li><svg viewBox="0 0 20 20" aria-hidden="true"><path d="M2 7c0-2 3.5-3.5 8-3.5S18 5 18 7v1.5h-4V7c-1-.6-2.4-.8-4-.8S7 6.4 6 7v1.5H2zM5 10h10l2 6H3zM10 11.5a2 2 0 1 0 0 4 2 2 0 0 0 0-4z"/></svg>02 9364 2710</li>
        <li><svg viewBox="0 0 20 20" aria-hidden="true"><path d="M6 1h8a1 1 0 0 1 1 1v16a1 1 0 0 1-1 1H6a1 1 0 0 1-1-1V2a1 1 0 0 1 1-1zm1 2v11h6V3zm3 12.5a1.2 1.2 0 1 0 0 2.4 1.2 1.2 0 0 0 0-2.4z"/></svg>02 8472 3159</li>
        <li class="email"><svg viewBox="0 0 20 20" aria-hidden="true"><path d="M2 5h16v1.2l-8 5-8-5zM2 8l8 5 8-5v7H2z"/></svg>paul@qvlegal.com.au</li>
      </ul>
    </div>
    <div class="web-band">www.qvlegal.com.au</div>
  </section>

  <section class="card card-back">
    <div class="brand">
      <span class="brand-mark"></span>
      <p class="brand-name">QUAYVIEW</p>
      <p class="brand-sub">LEGAL</p>
    </div>
  </section>
</body>
</html>
```